Copperleaf Roofing Business Card

This is my current business card. But I’d like to make some changes. Somewhere on the card I’d like to list some of the services we offer. Maybe on the back? But I’d still like to keep the red. White and black modern look.

-residential & commercial roofing
-Roof Repairs & Maintenance
-Storm Damage & Insurance Claims specialist
-Christmas Lights and permanent Christmas lights
Fencing. Windows. Gutters. Siding. Sheetrock, painting.

```html
<!DOCTYPE html>
<html lang="en">
<head>
<meta charset="utf-8">
<title>Copperleaf Roofing Business Card</title>
<link href="https://fonts.googleapis.com/css2?family=Lato:wght@400;700;900&family=Michroma&display=swap" rel="stylesheet">
<style>
  :root {
    --stage: #3a3a3a;
    --card-black: #050505;
    --card-white: #ffffff;
    --brand-red: #e3100f;
    --deep-red: #8c0b0b;
    --ink: #111111;
    --paper-text: #f4f4f4;
  }
  * { margin: 0; padding: 0; box-sizing: border-box; }
  html, body { width: 1200px; height: 694px; overflow: hidden; }
  body {
    background: var(--stage);
    font-family: "Lato", sans-serif;
    position: relative;
  }
  .card {
    position: absolute;
    top: 187px;
    width: 560px;
    height: 320px;
    border-radius: 18px;
    overflow: hidden;
  }
  .card-back { left: 25px; background: var(--card-black); }
  .card-front { left: 615px; background: var(--card-white); }

  .edge-band {
    position: absolute;
    left: 0; right: 0; bottom: 0;
    height: 18px;
    background: linear-gradient(90deg, var(--deep-red), var(--brand-red) 50%, var(--deep-red));
  }

  .brand-mark {
    position: absolute;
    width: 96px; height: 96px;
    border-radius: 50%;
    background: var(--brand-red);
  }
  .brand-name {
    position: absolute;
    font-family: "Lato", sans-serif;
    font-weight: 900;
    text-transform: uppercase;
    text-align: center;
    line-height: 1.1;
    letter-spacing: 1px;
  }

  /* back side */
  .card-back .brand-mark { left: 85px; top: 58px; border: 3px solid #fff; }
  .card-back .brand-name {
    left: 20px; width: 220px; top: 172px;
    font-size: 21px; color: var(--paper-text);
  }
  .divider {
    position: absolute;
    width: 2px;
    background: linear-gradient(var(--card-black), var(--brand-red) 30%, var(--brand-red) 70%, transparent);
  }
  .card-back .divider { left: 262px; top: 40px; height: 230px; transform: rotate(-14deg); }

  .service-list {
    position: absolute;
    left: 290px; top: 52px;
    list-style: none;
    color: var(--paper-text);
    font-size: 15px;
    line-height: 1.42;
  }
  .service-list li { position: relative; padding-left: 14px; }
  .service-list li::before {
    content: "";
    position: absolute; left: 0; top: 8px;
    width: 6px; height: 6px; border-radius: 50%;
    background: var(--brand-red);
  }
  .service-list li.plain::before { display: none; }

  /* front side */
  .card-front .brand-mark { left: 292px; top: 30px; }
  .card-front .brand-name {
    left: 250px; width: 260px; top: 134px;
    font-size: 21px; color: var(--brand-red);
  }
  .holder {
    position: absolute;
    left: 40px; top: 232px;
    text-align: right;
    width: 200px;
  }
  .holder-name {
    font-family: "Michroma", sans-serif;
    font-size: 17px;
    color: var(--brand-red);
    letter-spacing: 1px;
  }
  .holder-name .surname { color: var(--ink); }
  .holder-role { font-size: 15px; color: var(--ink); margin-top: 2px; }
  .card-front .divider { left: 262px; top: 206px; height: 90px; background: var(--brand-red); transform: rotate(-10deg); }

  .contact-list {
    position: absolute;
    left: 288px; top: 206px;
    list-style: none;
    font-size: 15px;
    color: var(--ink);
  }
  .contact-list li {
    display: flex; align-items: center; gap: 9px;
    height: 26px;
  }
  .contact-list svg { width: 15px; height: 15px; flex: none; }
</style>
</head>
<body>

<section class="card card-back" aria-label="Card back">
  <div class="brand-mark" aria-hidden="true"></div>
  <div class="brand-name">Copperleaf<br>Roofing Co.</div>
  <div class="divider" aria-hidden="true"></div>
  <ul class="service-list">
    <li>Residential &amp; commercial roofing</li>
    <li>Roof Repairs &amp; Maintenance</li>
    <li>Storm Damage &amp; Insurance</li>
    <li class="plain">Claims specialist</li>
    <li>Christmas Lights and</li>
    <li class="plain">permanent Christmas lights</li>
    <li>Fencing. Windows. Gutters.</li>
    <li class="plain">Siding. Sheetrock, painting.</li>
  </ul>
  <div class="edge-band" aria-hidden="true"></div>
</section>

<section class="card card-front" aria-label="Card front">
  <div class="brand-mark" aria-hidden="true"></div>
  <div class="brand-name">Copperleaf<br>Roofing Co.</div>

  <div class="holder">
    <div class="holder-name">DANA <span class="surname">WHITFIELD</span></div>
    <div class="holder-role">Owner</div>
  </div>

  <div class="divider" aria-hidden="true"></div>

  <ul class="contact-list">
    <li>
      <svg viewBox="0 0 16 16" aria-hidden="true"><path fill="#e3100f" d="M3.6 1.2l2.3 2.6-1.3 1.6c.8 1.9 2.2 3.3 4.1 4.1l1.6-1.3 2.6 2.3-1.2 2.4C6.6 12.6 3.4 9.4 1.2 2.4z"/></svg>
      555-014-2290
    </li>
    <li>
      <svg viewBox="0 0 16 16" aria-hidden="true"><rect x="1" y="3" width="14" height="10" fill="#e3100f"/><path d="M1 3l7 6 7-6" fill="none" stroke="#fff" stroke-width="1.4"/></svg>
      dana@copperleafroofing.co
    </li>
    <li>
      <svg viewBox="0 0 16 16" aria-hidden="true"><circle cx="8" cy="8" r="6.5" fill="none" stroke="#e3100f" stroke-width="1.6"/><ellipse cx="8" cy="8" rx="2.8" ry="6.5" fill="none" stroke="#e3100f" stroke-width="1.2"/><path d="M1.5 8h13" stroke="#e3100f" stroke-width="1.2"/></svg>
      www.copperleafroofing.co
    </li>
  </ul>

  <div class="edge-band" aria-hidden="true"></div>
</section>

</body>
</html>
```